Automotive component supplier needs a business card design

We need a business card design for our company called Velran Global Components Ltd based in the UK. We are a supplier of interior and exterior components to premium car manufacturers such as Corvel Ashby, Hadley Fenn, Marquist and Tavarelli. We would like to see a modern business card design that uses the colour blue.

Target Market(s)

Premium automotive car manufacturers.

Industry/Entity Type

Automotive

Contact Information for Business Card

Company Name : Velran Global Components Limited
Address: 17 Marlow Yard, Upper Heath, Warwick, CV31 8QL, United Kingdom
Web Address : www.velrancomponents-example.co.uk

Font styles to use
Other font styles liked:
• Helvetica

Colors
3176b5
0255a3
85acd3
cfdeed
cee9f5
85cae6
34a6d7
0692cd
9bcb3c

Requirements
Must have
• Clear company logo and a mixture of blue colours.
Nice to have
• A high quality modern image.
Should not have
• Multiple colours.

```html
<!DOCTYPE html>
<html lang="en">
<head>
<meta charset="utf-8">
<title>Velran Global Components – Business Card</title>
<link rel="stylesheet" href="https://fonts.googleapis.com/css2?family=Montserrat:wght@400;500;600&display=swap">
<style>
  :root {
    --blue-deep: #0255a3;
    --blue-mid: #3176b5;
    --blue-bright: #0692cd;
    --blue-sky: #34a6d7;
    --green: #9bcb3c;
    --ink: #2a3440;
    --paper: #ffffff;
    --stage: #e9eef3;
  }
  * { box-sizing: border-box; margin: 0; padding: 0; }
  html, body { width: 1200px; height: 1000px; overflow: hidden; }
  body {
    background: var(--stage);
    font-family: "Montserrat", Helvetica, Arial, sans-serif;
    position: relative;
  }
  .card {
    position: absolute;
    left: 250px;
    width: 700px;
    height: 400px;
    border-radius: 22px;
    overflow: hidden;
    box-shadow: 0 10px 30px rgba(20, 40, 70, 0.18);
    background: var(--paper);
  }
  .card--front { top: 55px; }
  .card--back { top: 535px; }
  .card__shapes { position: absolute; inset: 0; width: 100%; height: 100%; }

  .wordmark { position: absolute; font-weight: 600; line-height: 1; }
  .wordmark__name { display: block; letter-spacing: 2px; }
  .wordmark__sub { display: block; letter-spacing: 3px; margin-top: 8px; }
  .wordmark__dot {
    position: absolute; width: 14px; height: 14px; border-radius: 50%;
    background: var(--green);
  }

  .card--front .wordmark { left: 175px; top: 140px; color: var(--paper); }
  .card--front .wordmark__name { font-size: 76px; }
  .card--front .wordmark__sub { font-size: 17px; }
  .card--front .wordmark__dot { left: -24px; top: 6px; }

  .card--back .wordmark { left: 60px; top: 62px; color: var(--blue-mid); }
  .card--back .wordmark__name { font-size: 58px; }
  .card--back .wordmark__sub { font-size: 13px; margin-top: 7px; }
  .card--back .wordmark__dot { left: -22px; top: 4px; }

  .person { position: absolute; right: 60px; top: 58px; text-align: right; }
  .person__name { font-size: 24px; font-weight: 600; color: var(--blue-bright); letter-spacing: 1px; }
  .person__role { font-size: 13px; color: var(--green); margin-top: 4px; }

  .address {
    position: absolute; right: 60px; top: 128px; text-align: right;
    font-size: 14px; line-height: 1.45; color: var(--ink);
  }

  .contacts {
    position: absolute; left: 40px; top: 265px; list-style: none;
    font-size: 14px; line-height: 1; color: var(--ink);
  }
  .contacts li { display: flex; align-items: center; gap: 14px; height: 23px; }
  .contacts svg { width: 12px; height: 12px; flex: none; }
</style>
</head>
<body>

<section class="card card--front" aria-label="Card front">
  <svg class="card__shapes" viewBox="0 0 700 400" preserveAspectRatio="none" aria-hidden="true">
    <defs>
      <linearGradient id="frontBlue" x1="0" y1="0" x2="1" y2="1">
        <stop offset="0" stop-color="#0255a3"/>
        <stop offset="1" stop-color="#3176b5"/>
      </linearGradient>
    </defs>
    <rect width="700" height="400" fill="url(#frontBlue)"/>
    <polygon points="700,352 300,368 300,376 700,360" fill="var(--green)"/>
    <polygon points="0,345 250,345 300,368 300,400 0,400" fill="var(--paper)"/>
    <polygon points="300,376 700,360 700,400 300,400" fill="var(--paper)"/>
  </svg>
  <div class="wordmark">
    <span class="wordmark__dot"></span>
    <span class="wordmark__name">VELRAN</span>
    <span class="wordmark__sub">GLOBAL COMPONENTS</span>
  </div>
</section>

<section class="card card--back" aria-label="Card back">
  <svg class="card__shapes" viewBox="0 0 700 400" preserveAspectRatio="none" aria-hidden="true">
    <line x1="40" y1="150" x2="640" y2="150" stroke="var(--blue-mid)" stroke-width="1.2"/>
    <line x1="640" y1="150" x2="700" y2="132" stroke="var(--blue-mid)" stroke-width="1.2"/>
    <line x1="40" y1="250" x2="700" y2="250" stroke="var(--blue-mid)" stroke-width="1.2"/>
    <polygon points="0,388 470,374 470,382 0,400" fill="var(--green)"/>
    <polygon points="505,262 700,262 700,400 480,400" fill="var(--blue-deep)"/>
  </svg>

  <div class="wordmark">
    <span class="wordmark__dot"></span>
    <span class="wordmark__name">VELRAN</span>
    <span class="wordmark__sub">GLOBAL COMPONENTS</span>
  </div>

  <div class="person">
    <p class="person__name">MARTEN HOLLOWAY</p>
    <p class="person__role">Director</p>
  </div>

  <address class="address" style="font-style:normal">
    17 Marlow Yard<br>
    Upper Heath, Warwick<br>
    CV31 8QL, United Kingdom
  </address>

  <ul class="contacts">
    <li>
      <svg viewBox="0 0 12 12"><path d="M3 1l2 2.5-1.2 1.2a6 6 0 0 0 3.5 3.5L8.5 7 11 9l-1.5 2A9 9 0 0 1 1 2.5z" fill="var(--green)"/></svg>
      +330 5812-3904
    </li>
    <li>
      <svg viewBox="0 0 12 12"><rect x="3" y="0.5" width="6" height="11" rx="1.2" fill="none" stroke="var(--green)" stroke-width="1.3"/><circle cx="6" cy="9.5" r="0.8" fill="var(--green)"/></svg>
      +330 5817-2261
    </li>
    <li>
      <svg viewBox="0 0 12 12"><rect x="0.7" y="2" width="10.6" height="8" fill="none" stroke="var(--green)" stroke-width="1.3"/><path d="M1 2.5l5 4 5-4" fill="none" stroke="var(--green)" stroke-width="1.3"/></svg>
      info@velrancomponents-example.co.uk
    </li>
    <li>
      <svg viewBox="0 0 12 12"><circle cx="6" cy="6" r="5.2" fill="none" stroke="var(--green)" stroke-width="1.2"/><ellipse cx="6" cy="6" rx="2.2" ry="5.2" fill="none" stroke="var(--green)" stroke-width="1"/><line x1="0.8" y1="6" x2="11.2" y2="6" stroke="var(--green)" stroke-width="1"/></svg>
      www.velrancomponents-example.co.uk
    </li>
  </ul>
</section>

</body>
</html>
```